Real Estate Webpage Design

We have an existing website: ferndaleestatecollective.com.au
We focus customised service mainly on Property Management and second-hand property sales.
We are not entirely happy about the current design and layout can stay roughly the same as the back end coding is linked to a CRM system.
We would like to see the design are more reachable to our clients and appearing.
Please check our Website Design Draft for more details.

Industry/Entity Type

Real estate Agency

Number of Pages Required

5+ page

Font styles to use
Sans Serif

Colors

Designer to choose colors to be used in the design.

```html
<!DOCTYPE html>
<html lang="en">
<head>
<meta charset="utf-8">
<title>Appraisal – Ferndale Collective</title>
<link href="https://fonts.googleapis.com/css2?family=Poppins:wght@300;400;500;600;700&family=Roboto:wght@400;500&display=swap" rel="stylesheet">
<style>
:root{
  --gold:#f9b115;
  --navy:#0e2f4d;
  --ink:#1f3550;
  --muted:#8a8f99;
  --page:#fdfcfa;
  --line:#e3e3e3;
}
*{margin:0;padding:0;box-sizing:border-box}
html,body{width:1137px;height:1200px;overflow:hidden;background:var(--page);font-family:'Poppins',sans-serif;color:var(--ink)}
.canvas{position:relative;width:1137px;height:1200px}
.abs{position:absolute}

.header{position:absolute;left:0;top:0;width:1137px;height:57px;background:#fff}
.brand-box{position:absolute;left:57px;top:0;width:213px;height:71px;background:#fff;z-index:3;display:flex;align-items:center;gap:8px;padding-left:16px}
.brand-dot{width:24px;height:24px;border-radius:50%;background:var(--gold)}
.brand-name{font-weight:600;font-size:17px;color:var(--gold);line-height:1.1}
.nav a{position:absolute;top:22px;font-size:13px;color:var(--ink);text-decoration:none;font-weight:400;white-space:nowrap}
.nav a.active{color:var(--gold)}
.nav a.active::after{content:"";position:absolute;left:0;right:0;top:33px;height:2px;background:var(--gold)}
.btn-add{position:absolute;left:960px;top:17px;width:120px;height:33px;background:var(--gold);color:#fff;font-size:13px;display:flex;align-items:center;justify-content:center;border-left:2px solid var(--navy)}

.hero{position:absolute;left:0;top:57px;width:1137px;height:314px;background:linear-gradient(100deg,#3d4a3a 0%,#6a5a48 30%,#2c3a4a 55%,#8fa2b0 75%,#4f6b3d 100%)}
.hero-title{position:absolute;left:58px;top:186px;font-size:34px;font-weight:700;color:var(--gold)}
.hero-sub{position:absolute;left:58px;top:238px;font-family:'Roboto',sans-serif;font-size:12.5px;color:#fff}

.navy-block{left:57px;top:422px;width:76px;height:378px;background:var(--navy)}
.photo{left:101px;top:460px;width:446px;height:328px;background:linear-gradient(180deg,#6d7fb8 0%,#d9a79a 25%,#9aa3a8 45%,#8b8e90 75%,#6b7a55 100%)}
.intro-title{left:601px;top:476px;font-size:25px;font-weight:400;color:var(--gold);white-space:nowrap}
.intro-text{left:602px;top:510px;width:440px;font-size:13px;line-height:21px;color:var(--muted)}
.card{left:598px;top:572px;width:461px;height:192px;background:#fff}
.card-title{position:absolute;left:26px;top:30px;font-size:16px;font-weight:500;color:var(--navy)}
.card-input{position:absolute;left:26px;top:65px;width:405px;height:43px;border:1px solid var(--gold);font-family:'Roboto',sans-serif;font-size:12.5px;color:var(--muted);padding:13px 16px}
.card-btn{position:absolute;left:168px;top:135px;width:124px;height:33px;background:var(--gold);color:#fff;font-size:13px;font-weight:600;display:flex;align-items:center;justify-content:center;border-left:2px solid var(--navy);border-top:2px solid var(--navy)}

.f-brand{left:57px;top:924px;display:flex;align-items:center;gap:8px}
.f-about{left:58px;top:982px;width:200px;font-family:'Roboto',sans-serif;font-size:11px;line-height:21px;color:var(--ink)}
.f-title{font-size:12px;color:var(--gold)}
.f-links{left:318px;top:944px;list-style:none}
.f-links li{font-size:11px;height:27.5px;color:var(--ink)}
.contact-row{display:flex;gap:12px;font-family:'Roboto',sans-serif;font-size:11px;line-height:19px;color:var(--ink)}
.contact-row b{font-weight:500}
.socials{left:843px;top:952px;display:flex;gap:14px}
.socials span{width:37px;height:37px;border-radius:50%;border:1.5px solid var(--gold)}
.socials span:first-child{background:var(--gold)}

.bottom{left:0;top:1163px;width:1137px;height:37px;border-top:1px solid var(--line);font-family:'Roboto',sans-serif;font-size:11px;color:var(--ink)}
.bottom span{position:absolute;top:12px;white-space:nowrap}
</style>
</head>
<body>
<div class="canvas">
  <header class="header">
    <nav class="nav">
      <a style="left:308px">Home</a>
      <a style="left:373px">About Us</a>
      <a style="left:455px">Landload</a>
      <a style="left:538px">Tenant</a>
      <a style="left:605px">Make a Switch</a>
      <a style="left:723px">Property Sales</a>
      <a class="active" style="left:842px">Appraisal now</a>
    </nav>
    <div class="btn-add">Add Properties</div>
  </header>
  <div class="brand-box"><span class="brand-dot"></span><span class="brand-name">Ferndale<br>Collective</span></div>

  <section class="hero" role="img" aria-label="Modern two-storey timber and dark-clad house surrounded by trees">
    <h1 class="hero-title">Appraisal</h1>
    <p class="hero-sub">Your local real estate property group</p>
  </section>

  <div class="abs navy-block"></div>
  <div class="abs photo" role="img" aria-label="Two-storey suburban home with garage and hedge at sunset"></div>
  <h2 class="abs intro-title">Lorem Ipsum is simply dummy Text</h2>
  <p class="abs intro-text">Lorem Ipsum is simply dummy text of the printing and typesetting industry. Lorem Ipsum has been the industry's.</p>
  <div class="abs card">
    <h3 class="card-title">Find Your Property Adress</h3>
    <div class="card-input">Start to typing find your Property Adess...</div>
    <div class="card-btn">To Be Continue</div>
  </div>

  <div class="abs f-brand"><span class="brand-dot"></span><span class="brand-name" style="font-size:18px">Ferndale<br>Collective</span></div>
  <p class="abs f-about">Lorem ipsum dolor sit amet, consectetur adipiscing elit, sed do eiusmod tempor...</p>

  <div class="abs f-title" style="left:314px;top:918px">Site Map</div>
  <ul class="abs f-links">
    <li>Home</li><li>About Us</li><li>Landload</li><li>Tenant</li><li>Make a Switch</li><li>Property Sales</li><li>Appraisal now</li>
  </ul>

  <div class="abs f-title" style="left:581px;top:918px">Contact Us</div>
  <div class="abs contact-row" style="left:580px;top:953px">
    <svg width="18" height="22" viewBox="0 0 18 22" fill="none" stroke="#1f3550" stroke-width="1.2"><path d="M9 21s7-7 7-12A7 7 0 0 0 2 9c0 5 7 12 7 12z"/><circle cx="9" cy="9" r="2.5"/></svg>
    <span>18/4 Wattlebrook Rd,<br>Ferndale, ACT, 2618</span>
  </div>
  <div class="abs contact-row" style="left:580px;top:997px">
    <svg width="18" height="18" viewBox="0 0 18 18" fill="none" stroke="#1f3550" stroke-width="1.2"><path d="M4 1l3 4-2 2c1 3 3 5 6 6l2-2 4 3-2 3C8 17 1 10 1 3z"/></svg>
    <span><b>02 6000 1234</b><br><b>02 6000 5678</b></span>
  </div>
  <div class="abs contact-row" style="left:580px;top:1050px">
    <svg width="20" height="15" viewBox="0 0 20 15" fill="none" stroke="#1f3550" stroke-width="1.2"><rect x="1" y="1" width="18" height="13"/><path d="M1 1l9 7 9-7"/></svg>
    <span>info@ferndalecollective.com</span>
  </div>

  <div class="abs f-title" style="left:843px;top:918px">Social Media</div>
  <div class="abs socials" aria-label="Social media links"><span></span><span></span><span></span><span></span></div>

  <footer class="abs bottom">
    <span style="left:67px">2022© Ferndale Collective Properties. All right reserved.</span>
    <span style="left:623px">Privacy</span>
    <span style="left:695px">Complaint Handling &amp; Dispute Resolution</span>
    <span style="left:951px">Due Diligence Checklist</span>
  </footer>
</div>
</body>
</html>
```